RW Holloway LLC Business Card - Civil Engineering & Consulting Firm

We need a Business Card that is elegant, and masculine.  It is our Professional Civil Engineering & Consulting Company located in San Antonio TX (Not s construction or builder firm- no gears & no tool images please). We provide civil engineering services including  commercial site plans, grading and drainage plans, utility plans, hydraulics and hydrology, land planning, utility coordination, and other general civil engineering services related to commercial and residential development.
We have 2 existing Logos. We would like to convey reliability, strength, trustworthiness and attention to detail.  Blues and orange tones as per logo We are OK with the use of a darker blue in the mix.  We have 2 logo versions - Full Company Name Logo to go on the back of card, & Small Icon Logo for the front w/ personal Info.

Target Market(s)
Architects, Real Estate Developers, Other Strctural Engineers, Surveyers, General Contractors
Industry/Entity Type
Professional Civil Engineering
Contact Information for Business Card
Name, Position, Address, Cell & Office #, email, and company website
Font styles to use
Other font styles liked:
- Avian
Requirements
Should not have
- No Tools, No Gears, no Cranes, or Construction Equipment.

```html
<!DOCTYPE html>
<html lang="en">
<head>
<meta charset="utf-8">
<title>RW Holloway LLC – Business Card</title>
<link rel="stylesheet" href="https://fonts.googleapis.com/css2?family=Montserrat:wght@400;500;700&family=Arimo:wght@400&display=swap">
<style>
  :root {
    --sky-blue: #79acd9;
    --brand-orange: #f0902b;
    --ink: #1d1d1d;
    --paper: #ffffff;
    --backdrop: #e9e6e1;
  }
  * { box-sizing: border-box; margin: 0; padding: 0; }
  html, body {
    width: 1200px; height: 900px; overflow: hidden;
    background: var(--backdrop);
  }
  .canvas {
    position: relative; width: 1200px; height: 900px;
    display: flex; flex-direction: column; align-items: center; justify-content: center; gap: 60px;
  }
  .card {
    position: relative; width: 560px; height: 320px; overflow: hidden;
    box-shadow: 0 6px 18px rgba(0,0,0,0.25);
  }
  /* Back of card */
  .card--back {
    background: linear-gradient(200deg, var(--brand-orange) 0%, #c9a27a 40%, #a2a9ac 60%, var(--sky-blue) 85%);
    display: flex; flex-direction: column; align-items: center; justify-content: center; gap: 12px;
  }
  .wordmark {
    font-family: "Montserrat", sans-serif; font-weight: 400;
    font-size: 38px; letter-spacing: 3px; color: var(--paper); white-space: nowrap;
  }
  .tagline {
    font-family: "Montserrat", sans-serif; font-weight: 400;
    font-size: 11px; letter-spacing: 6px; text-transform: uppercase; color: var(--paper); white-space: nowrap;
  }
  /* Front of card */
  .card--front { background: var(--paper); }
  .card__waves { position: absolute; inset: 0; }
  .person { position: absolute; left: 40px; top: 40px; }
  .person__name {
    font-family: "Montserrat", sans-serif; font-weight: 700; font-size: 19px;
    text-transform: uppercase; color: var(--sky-blue); letter-spacing: 0.3px; white-space: nowrap;
  }
  .person__name .surname { color: var(--brand-orange); }
  .person__role {
    font-family: "Arimo", sans-serif; font-size: 14px; color: var(--ink); margin-top: 2px;
  }
  .front-brand {
    position: absolute; right: 30px; top: 58px; text-align: right;
  }
  .front-brand .wordmark { font-size: 21px; color: var(--sky-blue); letter-spacing: 1.5px; }
  .front-brand .tagline { font-size: 7.5px; letter-spacing: 3.5px; color: var(--brand-orange); margin-top: 6px; }
  .contact {
    position: absolute; left: 52px; top: 116px;
    font-family: "Arimo", sans-serif; font-size: 14px; color: var(--ink); line-height: 1.5;
  }
  .contact__row { display: flex; align-items: center; gap: 10px; }
  .contact__icon { width: 17px; height: 17px; flex: none; }
  .contact__address { margin-top: 10px; }
  .website {
    position: absolute; right: 30px; bottom: 40px;
    font-family: "Arimo", sans-serif; font-size: 14px; color: var(--paper); letter-spacing: 0.3px;
  }
</style>
</head>
<body>
<main class="canvas">

  <section class="card card--back" aria-label="Card back">
    <p class="wordmark">RW Holloway LLC</p>
    <p class="tagline">Consulting Engineers</p>
  </section>

  <section class="card card--front" aria-label="Card front">
    <svg class="card__waves" viewBox="0 0 560 320" preserveAspectRatio="none" aria-hidden="true">
      <path d="M0,266 C150,270 280,236 380,176 C290,244 160,284 0,286 Z" fill="var(--brand-orange)"/>
      <path d="M0,290 C170,284 300,244 400,184 C460,148 510,124 560,110 L560,320 L0,320 Z" fill="var(--sky-blue)"/>
      <path d="M0,290 C170,284 300,244 400,184 C460,148 510,124 560,110" fill="none" stroke="var(--paper)" stroke-width="3"/>
    </svg>

    <div class="person">
      <p class="person__name">Marcus <span class="surname">Delaney</span></p>
      <p class="person__role">Managing Director</p>
    </div>

    <div class="front-brand">
      <p class="wordmark">RW Holloway LLC</p>
      <p class="tagline">Consulting Engineers</p>
    </div>

    <div class="contact">
      <p class="contact__row">
        <svg class="contact__icon" viewBox="0 0 24 24" aria-hidden="true"><path d="M6.6 10.8a15 15 0 0 0 6.6 6.6l2.2-2.2a1 1 0 0 1 1-.25 11.4 11.4 0 0 0 3.6.57 1 1 0 0 1 1 1V20a1 1 0 0 1-1 1A17 17 0 0 1 3 4a1 1 0 0 1 1-1h3.5a1 1 0 0 1 1 1c0 1.250.2 2.45.57 3.57a1 1 0 0 1-.25 1z" fill="var(--sky-blue)"/></svg>
        044-210 387 615
      </p>
      <p class="contact__row">
        <svg class="contact__icon" viewBox="0 0 24 24" aria-hidden="true"><rect x="2" y="5" width="20" height="14" fill="var(--sky-blue)"/><path d="M2 5l10 8 10-8" fill="none" stroke="var(--paper)" stroke-width="1.6"/></svg>
        info@hollowayce.com
      </p>
      <p class="contact__address">1820, Alamo Ridge Drive<br>San Antonio, TX 78205</p>
    </div>

    <p class="website">www.hollowayce.com</p>
  </section>

</main>
</body>
</html>
```